Caldrift - Where every box finds its place!

Hello,
I'd like to update, re-vamp, and re-tool this current power point presentation with slightly more professional appearance as well as more accurately reflect the website -caldrift.com- color scheme and sleek design scheme. Please see attached.
We at Caldrift pride ourselves on seeking to rework an archaic business into something progressive, cost effective, more reliable, and easily accessible in todays fast growing market that has only gotten more expensive, more costly and less indirect over the last couple years.

Target Market(s)

New updated and hassle free moving opportunities no matter how large or how small in a market that begs for a change

Industry/Entity Type

Logistics/Moving

Requirements
Must have
• The current color scheme from the -caldrift.com- website as well as the inclusion of the current data on the sample power point presentation provided but with updated graphics

```html
<!DOCTYPE html>
<html lang="en">
<head>
<meta charset="utf-8">
<title>Caldrift – Company Presentation</title>
<link href="https://fonts.googleapis.com/css2?family=Poppins:ital,wght@0,300;0,400;0,500;0,600;0,700;1,400&display=swap" rel="stylesheet">
<style>
:root{
  --navy:#0f2f50;
  --navy-soft:#3b5876;
  --gold:#e3c25c;
  --yellow:#fbcf68;
  --blue:#3a74dc;
  --ink:#2b2b2b;
  --mist:#f1f1f3;
  --page:#ffffff;
}
*{box-sizing:border-box;margin:0;padding:0}
html,body{width:1200px;height:4138px;overflow:hidden;background:var(--page)}
body{position:relative;font-family:"Poppins",sans-serif;color:var(--ink)}
.slide{position:absolute;left:56px;width:1082px;height:608px;overflow:hidden;background:var(--mist);box-shadow:0 4px 14px rgba(0,0,0,.12)}
.abs{position:absolute}
.page-no{position:absolute;left:1003px;top:542px;width:56px;height:40px;background:#fff;border-radius:4px;box-shadow:0 2px 6px rgba(0,0,0,.18);font-size:18px;display:flex;align-items:center;justify-content:center;color:var(--ink)}
.brand{font-weight:700;color:var(--navy);font-size:50px;display:flex;align-items:center;gap:12px;letter-spacing:-.5px}
.brand-dot{width:22px;height:22px;background:var(--gold)}
.center{text-align:center}

/* slide 1 */
.s1{top:72px;background:linear-gradient(90deg,#eeeef1,#f6f6f8)}
.s1 .brand{left:140px;top:100px}
.s1 .welcome{left:100px;width:416px;top:276px;font-size:30px;color:var(--ink)}
.s1 .hero-name{left:60px;width:500px;top:336px;font-size:74px;font-weight:700;color:var(--gold)}
.s1 .tagline{left:60px;width:500px;top:448px;font-size:23px;font-style:italic;color:var(--navy)}

/* slide 2 */
.s2{top:752px;background:linear-gradient(90deg,#eeeef1,#f3f3f5)}
.s2 .label{left:40px;top:272px;font-size:27px;color:#fff;letter-spacing:.5px}
.s2 .about{left:236px;width:320px;top:136px;font-size:13px;line-height:27px;color:#333}
.s2 .about p+p{margin-top:8px}

/* slide 3 */
.s3{top:1432px;background:#f6f7f8}
.s3 .band-title{left:40px;width:450px;top:236px;font-size:32px;font-weight:600;color:#fff}
.s3 .band-text{left:30px;width:470px;top:296px;font-size:14px;line-height:27px;color:#fff}
.pillar{position:absolute;color:#fff;text-align:center}
.pillar h3{font-size:16px;font-weight:600;margin-bottom:12px}
.pillar p{font-size:13px;line-height:27px}
.pillar .arrow{font-size:20px;margin-top:4px}
.icon-dot{position:absolute;width:46px;height:46px;border-radius:50%;background:var(--navy-soft);display:flex;align-items:center;justify-content:center}

/* slide 4 */
.s4{top:2107px;background:#fff}
.slide-title{position:absolute;left:0;width:100%;text-align:center;font-size:33px;font-weight:700;color:var(--navy)}
.grid{position:absolute;left:75px;top:138px;width:936px;height:422px;display:grid;grid-template-columns:repeat(4,1fr);grid-template-rows:1fr 1fr}
.cell{position:relative;display:flex;flex-direction:column;align-items:center;justify-content:center;text-align:center}
.cell.fill{background:var(--yellow)}
.cell.note{background:#fff;border:2px solid var(--navy);padding:0 14px}
.cell.note h3{font-size:20px;font-weight:600;color:var(--navy);margin-bottom:10px}
.cell.note p{font-size:13px;line-height:27px;color:#444}
.cell .ghost{position:absolute;left:12px;top:6px;font-size:58px;font-weight:700;color:rgba(255,255,255,.35);line-height:1}
.cell .tip{position:absolute;left:50%;width:16px;height:16px;margin-left:-8px;transform:rotate(45deg)}
.tip.down{bottom:-8px;background:var(--yellow);z-index:2}
.tip.up{top:-8px;background:var(--yellow);z-index:2}

/* slide 5 */
.s5{top:2779px;background:linear-gradient(180deg,#f6f4ef,#f1efea)}
.card{position:absolute;width:294px;height:158px;background:#fff;box-shadow:0 3px 10px rgba(0,0,0,.08);display:flex;align-items:center;justify-content:center;text-align:center;font-size:24px;line-height:38px;color:#333;padding-top:14px}
.card.gold{border-top:6px solid var(--gold)}
.card.navy{border-top:6px solid var(--navy)}
.badge{position:absolute;width:74px;height:74px;border-radius:50%;display:flex;align-items:center;justify-content:center;font-size:22px;font-weight:600}
.badge.gold{background:var(--yellow);color:var(--navy)}
.badge.navy{background:var(--navy);color:var(--yellow)}

/* slide 6 */
.s6{top:3448px;background:#fff}
.s6 .brand{left:160px;top:50px}
.contact-panel{position:absolute;left:0;top:141px;width:600px;height:467px;background:var(--navy)}
.s6 .thanks{left:0;width:496px;top:200px;font-size:32px;font-weight:700;color:#fff}
.contact-row{position:absolute;left:37px;display:flex;align-items:center;gap:18px;color:#fff;font-size:17px;line-height:27px}
.contact-icon{width:64px;height:58px;background:#fff;border-radius:6px;display:flex;align-items:center;justify-content:center;flex:none}
</style>
</head>
<body>

<!-- Slide 1: Welcome -->
<section class="slide s1">
  <svg class="abs" width="1082" height="608" viewBox="0 0 1082 608" style="left:0;top:0">
    <circle cx="880" cy="232" r="318" fill="var(--gold)"/>
    <circle cx="912" cy="226" r="308" fill="#b88a5a"/>
  </svg>
  <div class="abs" role="img" aria-label="Movers in uniforms stacking cardboard boxes on a hand truck" style="left:604px;top:0;width:478px;height:540px"></div>
  <div class="abs brand"><span class="brand-dot"></span>Caldrift</div>
  <div class="abs welcome center">WELCOME TO</div>
  <div class="abs hero-name center">CALDRIFT</div>
  <div class="abs tagline center">MOVING FOR THE NEXT GENERATION</div>
</section>

<!-- Slide 2: About us -->
<section class="slide s2">
  <svg class="abs" width="1082" height="608" viewBox="0 0 1082 608" style="left:0;top:0">
    <defs>
      <linearGradient id="aboutGrad" x1="0" y1="0" x2="0" y2="1">
        <stop offset="0" stop-color="#f3cc5c"/>
        <stop offset="1" stop-color="#3a74dc"/>
      </linearGradient>
    </defs>
    <polygon points="0,0 240,280 0,608" fill="url(#aboutGrad)"/>
    <polyline points="14,40 226,286 14,560" fill="none" stroke="#8a8fa0" stroke-width="1.2" opacity=".6"/>
    <polygon points="612,0 1082,0 1082,608 536,608 580,300" fill="#c79d6e" role="img" aria-label="Two movers lifting cardboard boxes in a bright room"/>
    <polyline points="612,0 580,300" fill="none" stroke="var(--gold)" stroke-width="5"/>
    <polyline points="580,300 536,608" fill="none" stroke="var(--blue)" stroke-width="5"/>
  </svg>
  <div class="abs label">ABOUT US</div>
  <div class="abs about center">
    <p>Caldrift is the next logical evolution in professional moving. Professional moving clients have battled soaring prices, acute capacity problems and deteriorating service levels.</p>
    <p>Caldrift was founded by lifelong moving professionals who have developed the answer to better moving services. Poised as THE industry disruptor, we deliver faster, offer guaranteed prices and even offer no credit check financing options. We are a technology first organization using proprietary software to deliver moving's best service experience.</p>
  </div>
  <div class="page-no">02</div>
</section>

<!-- Slide 3: Vision -->
<section class="slide s3">
  <svg class="abs" width="1082" height="608" viewBox="0 0 1082 608" style="left:0;top:0">
    <defs>
      <linearGradient id="visionGrad" x1="0" y1="0" x2="1" y2="1">
        <stop offset="0" stop-color="#e7c35c"/>
        <stop offset=".55" stop-color="#7f95b4"/>
        <stop offset="1" stop-color="#3a74dc"/>
      </linearGradient>
    </defs>
    <polygon points="0,203 540,203 622,298 540,392 0,392" fill="url(#visionGrad)" role="img" aria-label="Calm sea at sunrise in gold and blue tones"/>
    <polygon points="518,0 746,0 746,196 632,290 518,196" fill="var(--navy)"/>
    <polygon points="746,203 1082,203 1082,392 746,392 648,298" fill="var(--navy)"/>
    <polygon points="518,608 746,608 746,402 632,306 518,402" fill="var(--navy)"/>
  </svg>
  <div class="abs band-title center">CALDRIFT VISION</div>
  <div class="abs band-text center">THE TRADITIONAL MOVING INDUSTRY IS BROKEN, OUTDATED, INEFFICIENT, AND UNABLE TO CHANGE.</div>

  <div class="pillar" style="left:518px;top:28px;width:228px">
    <h3>OUR VISION</h3>
    <p>Revolutionize an $86B<br>industry by providing<br>great value to everyone<br>involved</p>
    <div class="arrow">→</div>
  </div>
  <div class="pillar" style="left:800px;top:240px;width:234px">
    <h3>OUR MISSION</h3>
    <p>Disrupt a sleepy giant of an<br>inefficient industry</p>
    <div class="arrow">→</div>
  </div>
  <div class="pillar" style="left:518px;top:422px;width:228px">
    <h3>OUR GOAL</h3>
    <p>Becoming the moving<br>platform of choice</p>
    <div class="arrow">→</div>
  </div>

  <div class="icon-dot" style="left:607px;top:214px">
    <svg width="26" height="18" viewBox="0 0 26 18"><path d="M1 9 Q13 -4 25 9 Q13 22 1 9Z" fill="#fff"/><circle cx="13" cy="9" r="4" fill="var(--navy-soft)"/></svg>
  </div>
  <div class="icon-dot" style="left:697px;top:266px">
    <svg width="24" height="24" viewBox="0 0 24 24" fill="none" stroke="#fff" stroke-width="2"><circle cx="12" cy="12" r="10"/><circle cx="12" cy="12" r="5.5"/><circle cx="12" cy="12" r="1.5" fill="#fff"/></svg>
  </div>
  <div class="icon-dot" style="left:607px;top:340px">
    <svg width="24" height="22" viewBox="0 0 24 22" fill="#fff"><rect x="2" y="14" width="4" height="7"/><rect x="8" y="10" width="4" height="11"/><rect x="14" y="6" width="4" height="15"/><path d="M2 9 L10 4 L16 6 L22 1" stroke="#fff" stroke-width="1.6" fill="none"/></svg>
  </div>
  <div class="page-no">03</div>
</section>

<!-- Slide 4: Problems -->
<section class="slide s4">
  <h2 class="slide-title" style="top:52px">MOVING’S PROBLEMS</h2>
  <div class="grid">
    <div class="cell fill"><span class="ghost">01</span>
      <svg width="120" height="110" viewBox="0 0 120 110"><path d="M38 14 L58 14 L52 28 Q82 46 76 80 Q72 100 46 100 Q16 100 14 78 Q12 48 44 28Z" fill="var(--navy)"/><text x="45" y="80" font-family="Poppins,sans-serif" font-size="34" font-weight="700" fill="var(--yellow)" text-anchor="middle">$</text><rect x="74" y="50" width="34" height="10" rx="5" fill="var(--navy)"/><rect x="74" y="64" width="34" height="10" rx="5" fill="var(--navy)"/><rect x="74" y="78" width="34" height="10" rx="5" fill="var(--navy)"/><rect x="74" y="92" width="34" height="10" rx="5" fill="var(--navy)"/></svg>
      <span class="tip down"></span>
    </div>
    <div class="cell note"><h3>CAPACITY</h3><p>Long-haul driver shortages and limited equipment coupled with growing demand has pushed capacity to a crisis state</p></div>
    <div class="cell fill"><span class="ghost">03</span>
      <svg width="100" height="100" viewBox="0 0 100 100"><circle cx="50" cy="38" r="20" fill="var(--navy)"/><path d="M24 40 Q24 10 50 10 Q76 10 76 40" fill="none" stroke="var(--navy)" stroke-width="6"/><rect x="18" y="34" width="10" height="18" rx="4" fill="var(--navy)"/><rect x="72" y="34" width="10" height="18" rx="4" fill="var(--navy)"/><path d="M14 96 Q16 64 50 64 Q84 64 86 96Z" fill="var(--navy)"/></svg>
      <span class="tip down"></span>
    </div>
    <div class="cell note"><h3>TRANSPARANCY</h3><p>Too many margin layers…van line, agent, driver and help. In addition, charges are convoluted and confusing</p></div>

    <div class="cell note"><span class="tip up" style="background:#fff;border-left:2px solid var(--navy);border-top:2px solid var(--navy);display:none"></span><h3>COST</h3><p>Moving cost has skyrocketed over the last three years. Charges have increased 38% since 2018.</p></div>
    <div class="cell fill"><span class="ghost">02</span>
      <svg width="140" height="90" viewBox="0 0 140 90"><rect x="4" y="8" width="82" height="60" rx="3" fill="var(--navy)"/><path d="M90 26 L116 26 L136 48 L136 68 L90 68Z" fill="var(--navy)"/><path d="M98 32 L112 32 L124 46 L98 46Z" fill="var(--yellow)"/><circle cx="28" cy="72" r="12" fill="var(--navy)" stroke="var(--yellow)" stroke-width="4"/><circle cx="112" cy="72" r="12" fill="var(--navy)" stroke="var(--yellow)" stroke-width="4"/></svg>
      <span class="tip up" style="background:#fff;border:2px solid var(--navy);border-right:none;border-bottom:none"></span>
    </div>
    <div class="cell note"><h3>SERVICE</h3><p>Quality labor has been difficult to source and afford. Virtually all RMC’s report a decline in service quality</p></div>
    <div class="cell fill"><span class="ghost">04</span>
      <svg width="120" height="110" viewBox="0 0 120 110"><line x1="14" y1="100" x2="44" y2="70" stroke="var(--navy)" stroke-width="12" stroke-linecap="round"/><circle cx="74" cy="42" r="34" fill="var(--navy)"/><circle cx="74" cy="42" r="27" fill="var(--yellow)"/><path d="M54 42 Q74 22 94 42 Q74 62 54 42Z" fill="var(--navy)"/><circle cx="74" cy="42" r="6" fill="var(--yellow)"/></svg>
      <span class="tip up" style="background:#fff;border:2px solid var(--navy);border-right:none;border-bottom:none"></span>
    </div>
  </div>
  <div class="page-no">04</div>
</section>

<!-- Slide 5: Accomplishments -->
<section class="slide s5">
  <div class="abs" role="img" aria-label="Faded photo of a mover carrying boxes in a kitchen" style="left:0;top:0;width:1082px;height:608px"></div>
  <h2 class="slide-title" style="top:52px">WHAT CALDRIFT HAS ACCOMPLISHED</h2>
  <div class="card gold" style="left:56px;top:165px">Eliminate Capacity<br>Constraints</div>
  <div class="card navy" style="left:388px;top:165px">Reduce Costs</div>
  <div class="card gold" style="left:720px;top:165px">Improve Service<br>Levels</div>
  <div class="card navy" style="left:221px;top:392px">Simplify the Moving<br>Process</div>
  <div class="card gold" style="left:554px;top:392px">Break the Typical<br>Moving Mold</div>
  <div class="badge gold" style="left:166px;top:123px">01</div>
  <div class="badge navy" style="left:498px;top:123px">02</div>
  <div class="badge gold" style="left:830px;top:123px">03</div>
  <div class="badge navy" style="left:331px;top:350px">04</div>
  <div class="badge gold" style="left:664px;top:350px">05</div>
  <div class="page-no">05</div>
</section>

<!-- Slide 6: Thank you -->
<section class="slide s6">
  <div class="abs brand"><span class="brand-dot"></span>Caldrift</div>
  <div class="contact-panel"></div>
  <svg class="abs" width="1082" height="608" viewBox="0 0 1082 608" style="left:0;top:0">
    <polygon points="590,95 1082,95 1082,608 560,608" fill="#c08f5c" role="img" aria-label="Stack of cardboard boxes in an empty room"/>
    <polyline points="1082,84 590,84 520,150 560,608" fill="none" stroke="#f0d23a" stroke-width="8"/>
  </svg>
  <div class="abs thanks center">THANK YOU!</div>
  <div class="contact-row" style="top:261px">
    <span class="contact-icon"><svg width="22" height="30" viewBox="0 0 22 30"><path d="M11 1 C5 1 1 5 1 11 C1 19 11 29 11 29 C11 29 21 19 21 11 C21 5 17 1 11 1Z" fill="var(--navy)"/><circle cx="11" cy="11" r="4" fill="#fff"/></svg></span>
    482 Harbor Lane, Fairview City, ST 10482
  </div>
  <div class="contact-row" style="top:341px">
    <span class="contact-icon"><svg width="28" height="28" viewBox="0 0 24 24"><path d="M6.6 10.8a15.1 15.1 0 0 0 6.6 6.6l2.2-2.2a1 1 0 0 1 1-.25 11.4 11.4 0 0 0 3.6.57 1 1 0 0 1 1 1V20a1 1 0 0 1-1 1A17 17 0 0 1 3 4a1 1 0 0 1 1-1h3.5a1 1 0 0 1 1 1c0 1.25.2 2.45.57 3.57a1 1 0 0 1-.25 1z" fill="var(--navy)"/></svg></span>
    (800) 555-0142
  </div>
  <div class="contact-row" style="top:429px">
    <span class="contact-icon"><svg width="30" height="30" viewBox="0 0 30 30" fill="none" stroke="var(--navy)" stroke-width="2"><circle cx="15" cy="15" r="13"/><ellipse cx="15" cy="15" rx="6" ry="13"/><line x1="2" y1="15" x2="28" y2="15"/><line x1="4" y1="8" x2="26" y2="8"/><line x1="4" y1="22" x2="26" y2="22"/></svg></span>
    <span>caldrift.com<br>support@caldrift.com</span>
  </div>
</section>

</body>
</html>
```